MRT Property - Business Cards

Looking for a business card & general letterhead, signage etc design for our new logo.

Colours:
000a20
0056a2
00b5ef
0088ce
68cef2

Fonts:
Poppins
Karla

Please keep look and feel of new brand - example in the zip package I sent.

```html
<!DOCTYPE html>
<html lang="en">
<head>
<meta charset="utf-8">
<title>MRT Property – Business Cards</title>
<link href="https://fonts.googleapis.com/css2?family=Poppins:wght@400;500;600;700&family=Delius&display=swap" rel="stylesheet">
<style>
  :root {
    --ink: #000a20;
    --brand-navy: #0056a2;
    --brand-sky: #00b5ef;
    --brand-mid: #0088ce;
    --brand-light: #68cef2;
    --card-blue: #0b4fa0;
    --card-deep: #173f82;
    --paper: #ffffff;
    --backdrop: #ece8e1;
  }
  * { box-sizing: border-box; margin: 0; padding: 0; }
  html, body { width: 900px; height: 1200px; overflow: hidden; }
  body {
    position: relative;
    background: var(--backdrop);
    font-family: "Poppins", sans-serif;
    color: var(--ink);
  }
  .card {
    position: absolute;
    width: 742px;
    height: 440px;
    border-radius: 22px;
    overflow: hidden;
  }
  .card-front { left: 80px; top: 131px; background: var(--paper); }
  .card-back  { left: 78px; top: 638px; background: var(--card-blue); }

  .brand-lockup {
    position: absolute;
    display: flex;
    align-items: center;
    font-family: "Poppins", sans-serif;
    font-weight: 700;
    letter-spacing: 0.3px;
    white-space: nowrap;
    line-height: 1;
  }
  .brand-lockup .brand-dot { border-radius: 50%; flex: none; }

  .card-front .brand-lockup {
    left: 74px; top: 222px;
    width: 256px;
    gap: 10px;
    font-size: 26px;
    color: var(--brand-navy);
  }
  .card-front .brand-dot { width: 26px; height: 26px; background: var(--brand-navy); }

  .divider {
    position: absolute;
    left: 349px; top: 121px;
    width: 2px; height: 224px;
    background: var(--brand-navy);
  }
  .contact { position: absolute; left: 365px; top: 118px; }
  .contact .person-name {
    font-family: "Delius", cursive;
    font-size: 30px;
    color: var(--brand-navy);
    line-height: 1.2;
  }
  .contact .person-role { font-size: 15px; margin-top: 2px; }
  .contact .address { font-size: 15px; line-height: 22px; margin-top: 22px; }
  .contact .channels { list-style: none; margin-top: 20px; }
  .contact .channels li {
    display: flex; align-items: center; gap: 10px;
    font-size: 15px; height: 28px;
  }
  .contact .channels svg { width: 17px; height: 17px; fill: var(--brand-navy); flex: none; }

  .back-texture {
    position: absolute; inset: 0;
    background: linear-gradient(115deg, var(--brand-sky) 0%, var(--brand-mid) 22%, var(--card-blue) 50%, var(--card-deep) 100%);
    opacity: 0.55;
  }
  .card-back .brand-lockup {
    right: 92px; top: 322px;
    gap: 8px;
    font-size: 20px;
    color: var(--paper);
  }
  .card-back .brand-dot { width: 20px; height: 20px; background: var(--paper); }
</style>
</head>
<body>
  <section class="card card-front" aria-label="Business card front">
    <div class="brand-lockup"><span class="brand-dot"></span><span>MRT PROPERTY</span></div>
    <div class="divider"></div>
    <div class="contact">
      <p class="person-name">Daniel Harper</p>
      <p class="person-role">Mnaging Director</p>
      <p class="address">418 Maple Ridge Ave Suite<br>220 Dayton Ohio 45402</p>
      <ul class="channels">
        <li>
          <svg viewBox="0 0 24 24"><path d="M6.6 10.8a15 15 0 0 0 6.6 6.6l2.2-2.2a1 1 0 0 1 1-.25 11.4 11.4 0 0 0 3.6.57 1 1 0 0 1 1 1V20a1 1 0 0 1-1 1A17 17 0 0 1 3 4a1 1 0 0 1 1-1h3.5a1 1 0 0 1 1 1c0 1.25.2 2.45.57 3.57a1 1 0 0 1-.25 1z"/></svg>
          <span>1 (555) 214-7390</span>
        </li>
        <li>
          <svg viewBox="0 0 24 24"><path d="M3 5h18v2l-9 6-9-6z M3 8.5l9 6 9-6V19H3z"/></svg>
          <span>info@mrtproperty.com</span>
        </li>
        <li>
          <svg viewBox="0 0 24 24"><path d="M12 2a10 10 0 1 0 0 20 10 10 0 0 0 0-20zm-1 17.9A8 8 0 0 1 4.1 10.6L9 15.5v1a2 2 0 0 0 2 2zm6.9-2.5A2 2 0 0 0 16 16h-1v-3a1 1 0 0 0-1-1H8v-2h2a1 1 0 0 0 1-1V7h2a2 2 0 0 0 2-2v-.4a8 8 0 0 1 2.9 12.8z"/></svg>
          <span>www.mrtproperty.com</span>
        </li>
      </ul>
    </div>
  </section>

  <section class="card card-back" aria-label="Business card back">
    <div class="back-texture" role="img" aria-label="Repeating brand symbol pattern fading from light blue to deep blue"></div>
    <div class="brand-lockup"><span class="brand-dot"></span><span>MRT PROPERTY</span></div>
  </section>
</body>
</html>
```